Silver Bloom Marisol's Cleaning Service Business Cards Project

A business card with all contact details with logo design on there (already have a logo) eye catching Logo and contact info on one side, full logo on the back, must target upper class residential and corporate companies, fitness companies, still keep it on the feminine side of things , must look elegant

Target Market(s)

Upper class homes and corporate companies

Industry/Entity Type

Cleaning Service

Contact Information for Business Card

Name: Marisol Quenby
Position: Director
ABN: 31647209853
Email: marisolssilvercleaning@tidymail.example
Number: 0417906354

Font styles to use
Decorative

Colors

Designer to choose colors to be used in the design.

Requirements
Must have
• Available Sydney Wide, contact info and logo on one side, full logo on the back
Nice to have
• Professional appearance
Should not have
• Cheap advert looking stuff

```html
<!DOCTYPE html>
<html lang="en">
<head>
<meta charset="utf-8">
<title>Silver Bloom – Business Cards</title>
<link rel="stylesheet" href="https://fonts.googleapis.com/css2?family=Noto+Serif:wght@700&family=Roboto:wght@400&display=swap">
<style>
  :root {
    --backdrop: #2a2a2b;
    --card: #333c49;
    --teal: #5ec7c1;
    --white: #f4f6f8;
  }
  * { margin: 0; padding: 0; box-sizing: border-box; }
  html, body {
    width: 1200px; height: 900px; overflow: hidden;
    background: var(--backdrop);
  }
  .canvas {
    position: relative; width: 1200px; height: 900px;
  }
  .card {
    position: absolute; left: 250px; width: 700px; height: 400px;
    background: var(--card);
    border-radius: 2px;
    display: flex; flex-direction: column; align-items: center; justify-content: center;
    text-align: center;
  }
  .card--front { top: 40px; }
  .card--back { top: 465px; }

  .brand-dot {
    width: 18px; height: 18px; border-radius: 50%;
    background: var(--teal); margin-bottom: 22px;
  }
  .brand-name {
    font-family: "Noto Serif", Georgia, serif; font-weight: 700;
    color: var(--teal);
    text-transform: uppercase;
    font-size: 40px; letter-spacing: 2px; line-height: 1.1;
  }
  .brand-tagline {
    font-family: "Noto Serif", Georgia, serif; font-weight: 700;
    color: var(--teal);
    text-transform: uppercase;
    font-size: 13px; letter-spacing: 6px; margin-top: 8px;
  }

  .person-name {
    font-family: "Noto Serif", Georgia, serif; font-weight: 700;
    color: var(--teal); font-size: 34px; letter-spacing: 0.5px;
  }
  .person-role {
    font-family: "Roboto", Arial, sans-serif; color: var(--white);
    font-size: 19px; margin-top: 2px;
  }
  .divider {
    width: 50px; height: 2px; background: var(--white);
    margin: 22px 0 20px;
  }
  .contact {
    font-family: "Roboto", Arial, sans-serif; color: var(--white);
    font-size: 20px; line-height: 1.35;
    display: flex; align-items: center; gap: 8px; justify-content: center;
  }
  .contact svg { flex: none; }
  .abn { margin-top: 12px; }
  .abn-label { color: var(--teal); }
</style>
</head>
<body>
<main class="canvas">
  <section class="card card--front">
    <div class="brand-dot"></div>
    <p class="brand-name">Silver Bloom</p>
    <p class="brand-tagline">Marisol's Cleaning Service</p>
  </section>

  <section class="card card--back">
    <h1 class="person-name">Marisol Quenby</h1>
    <p class="person-role">Director</p>
    <div class="divider"></div>
    <p class="contact">
      <svg width="16" height="16" viewBox="0 0 24 24" aria-hidden="true"><path fill="#5ec7c1" d="M6.6 10.8a15.1 15.1 0 0 0 6.6 6.6l2.2-2.2a1 1 0 0 1 1-.25 11.4 11.4 0 0 0 3.6.57 1 1 0 0 1 1 1V20a1 1 0 0 1-1 1A17 17 0 0 1 3 4a1 1 0 0 1 1-1h3.5a1 1 0 0 1 1 1c0 1.25.2 2.45.57 3.57a1 1 0 0 1-.25 1z"/></svg>
      0417906354
    </p>
    <p class="contact">
      <svg width="22" height="16" viewBox="0 0 22 16" aria-hidden="true"><rect x="1" y="1" width="20" height="14" fill="none" stroke="#5ec7c1" stroke-width="1.6"/><path d="M1 1l10 8 10-8M1 15l7-6M21 15l-7-6" fill="none" stroke="#5ec7c1" stroke-width="1.6"/></svg>
      marisolssilvercleaning@tidymail.example
    </p>
    <p class="contact abn"><span class="abn-label">ABN :</span> 31647209853</p>
  </section>
</main>
</body>
</html>
```